Yard sign design for high end luxury home builder.

Need a design for signage on custom homes that are being built. I already have a logo that I am satisfied with that needs to be incorporated. I need the following incorporated in the design of the sign-
- Lic number 381526
- phone number (805) 555-0148‬
- quennbuilderscrew.com
- Logo/Branding

If possible it may be nice to have the following quote that is on are business cards-

Quote from Gerard of Norvelle-
HE WHO WORKS WITH HIS HANDS IS A LABORER.
HE WHO WORKS WITH HIS HANDS & HIS HEAD IS A CRAFTSMAN.
HE WHO WORKS WITH HIS HANDS & HIS HEAD & HIS HEART IS AN ARTISAN.
-GERARD OF NORVELLE

Target Market(s)

Archetect, Designers, Clients desiring to build a new home or remodel.

Colors
fde9d4
fee4d5
fabb94
fac994
faa54b
f68d4d
f37122
f78f20
f68e4e

Requirements
Must have
• - Lic number 381526
• - phone number (805) 555-0148‬
• - quennbuilderscrew.com
• - Logo/Branding
Nice to have
• Quote from Gerard of Norvelle-
• HE WHO WORKS WITH HIS HANDS IS A LABORER.
• HE WHO WORKS WITH HIS HANDS & HIS HEAD IS A CRAFTSMAN.
• HE WHO WORKS WITH HIS HANDS & HIS HEAD & HIS HEART IS AN ARTISAN.
• -GERARD OF NORVELLE
• OR the below statement-
• Craftsmen that Care
Should not have
• Any additional verbiage not specified above including any type of verbiage about what kind of company we are. For instance- Integrity, reputable... It's just all played out. Im just looking for a bitching design that has the info that compliments my logo/branding.

```html
<!DOCTYPE html>
<html lang="en">
<head>
<meta charset="utf-8">
<title>Quenn Builders Inc. – Yard Sign</title>
<link rel="stylesheet" href="https://fonts.googleapis.com/css2?family=Montserrat:wght@600;700&family=Roboto+Condensed:ital,wght@0,500;0,700;1,500&display=swap">
<style>
  :root {
    --canvas: #e9e6e2;
    --sign-white: #ffffff;
    --sign-mist: #e6e6e6;
    --brand-taupe: #8b7b69;
    --brand-mark: #7d6a56;
    --orange-deep: #f37122;
    --orange-mid: #f68d4d;
    --orange-bright: #f78f20;
    --orange-soft: #faa54b;
    --rule-grey: #d9d9d9;
    --ink: #111111;
    --paper: #ffffff;
  }
  * { box-sizing: border-box; margin: 0; padding: 0; }
  html, body { width: 1200px; height: 1000px; overflow: hidden; }
  body {
    background: var(--canvas);
    display: flex;
    align-items: center;
    justify-content: center;
  }
  .yard-sign {
    width: 620px;
    height: 820px;
    transform: scale(1.15);
    display: flex;
    flex-direction: column;
    box-shadow: 0 6px 24px rgba(0,0,0,.18);
    background: var(--sign-white);
  }
  .brand-panel {
    height: 468px;
    background: linear-gradient(to bottom, var(--sign-white) 40%, var(--sign-mist) 100%);
    display: flex;
    flex-direction: column;
    align-items: center;
    padding-top: 58px;
  }
  .brand-square {
    width: 230px;
    height: 230px;
    background: var(--brand-mark);
    margin-bottom: 34px;
  }
  .brand-name {
    font-family: "Montserrat", sans-serif;
    font-weight: 700;
    color: var(--brand-taupe);
    text-align: center;
    line-height: 1;
  }
  .brand-name .primary { display: block; font-size: 50px; letter-spacing: 4px; }
  .brand-name .secondary { display: block; font-size: 19px; letter-spacing: 2.5px; margin-top: 8px; }
  .accent-stripe {
    height: 7px;
    background: linear-gradient(to right, var(--orange-soft), var(--orange-mid));
    border-bottom: 3px solid var(--paper);
    height: 10px;
  }
  .contact-panel {
    height: 218px;
    background: var(--orange-deep);
    display: flex;
    flex-direction: column;
    align-items: center;
    padding-top: 18px;
  }
  .phone {
    font-family: "Roboto Condensed", sans-serif;
    font-weight: 700;
    font-size: 82px;
    line-height: 1;
    color: var(--paper);
    letter-spacing: 1px;
  }
  .website {
    font-family: "Montserrat", sans-serif;
    font-weight: 600;
    font-size: 33px;
    color: var(--ink);
    margin-top: 20px;
    line-height: 1;
  }
  .license {
    display: flex;
    align-items: center;
    gap: 14px;
    margin-top: 22px;
    font-family: "Montserrat", sans-serif;
    font-weight: 600;
    font-size: 20px;
    color: var(--ink);
    letter-spacing: 1px;
  }
  .license svg { display: block; }
  .divider {
    height: 6px;
    background: var(--rule-grey);
  }
  .quote-panel {
    flex: 1;
    background: linear-gradient(to right, var(--orange-mid), var(--orange-soft) 55%, var(--orange-mid));
    padding: 12px 24px 0;
    font-family: "Roboto Condensed", sans-serif;
    text-align: center;
  }
  .quote-text {
    font-weight: 500;
    font-size: 15px;
    line-height: 1.22;
    color: var(--ink);
  }
  .quote-source {
    text-align: right;
    font-style: italic;
    font-weight: 500;
    font-size: 13px;
    color: var(--paper);
    margin-top: 6px;
    letter-spacing: .5px;
  }
</style>
</head>
<body>
  <main class="yard-sign">
    <section class="brand-panel">
      <div class="brand-square"></div>
      <h1 class="brand-name">
        <span class="primary">QUENN</span>
        <span class="secondary">BUILDERS INC.</span>
      </h1>
    </section>
    <div class="accent-stripe"></div>
    <section class="contact-panel">
      <p class="phone">(805) 555-0148</p>
      <p class="website">www.quennbuilderscrew.com</p>
      <p class="license">
        <svg width="80" height="6" viewBox="0 0 80 6" aria-hidden="true"><polygon points="0,3 80,0 80,6" fill="#ffffff"/></svg>
        LIC NUMBER 381526
        <svg width="80" height="6" viewBox="0 0 80 6" aria-hidden="true"><polygon points="0,0 80,3 0,6" fill="#ffffff"/></svg>
      </p>
    </section>
    <div class="divider"></div>
    <section class="quote-panel">
      <blockquote class="quote-text">
        HE WHO WORKS WITH HIS HANDS IS A LABORER.<br>
        HE WHO WORKS WITH HIS HANDS &amp; HIS HEAD IS A CRAFTSMAN.<br>
        HE WHO WORKS WITH HIS HANDS &amp; HIS HEAD &amp; HIS HEART IS AN ARTISAN.
      </blockquote>
      <p class="quote-source">–GERARD OF NORVELLE</p>
    </section>
  </main>
</body>
</html>
```